Homemaking training schools needs a Business Card design

Designer, Hello!

No special requirements, good-looking enough.
--------------------------------------------------------------------------

Name: Marcus Dole
Chairman
Tel: 0574-71948263
Mobile: 13857420916
Email: kelvora@mailnest.example
Web: www.prt2019.example
Add: No.258, LanpingJie, BeiyuanQu, Ningbo, Zhejiang

LOGO
Ningbo PRT Homemaking Training School

Target Market(s)

pregnant women, mothers, infants, the elderly and families, including cleaning, cooking, nursing training.

Industry/Entity Type

Business

Contact Information for Business Card

Name: Marcus Dole
Chairman
Tel: 0574-71948263
Mobile: 13857420916
Email: kelvora@mailnest.example
Web: www.prt2019.example

LOGO

Font styles to use
Serif
Sans Serif
Decorative

Requirements
Nice to have
• Feels: clean, specifications, safety, comfort, warmth and happiness.

```html
<!DOCTYPE html>
<html lang="en">
<head>
<meta charset="utf-8">
<title>Pingrui Homemaking Business Card</title>
<link rel="stylesheet" href="https://fonts.googleapis.com/css2?family=Arimo:wght@400;700&display=swap">
<style>
  :root {
    --stage: #2b2b2d;
    --paper: #ffffff;
    --paper-shade: #eceef0;
    --brand-blue: #2f7bbd;
    --band-blue: #3a83c3;
    --band-blue-deep: #2d6fab;
    --accent-pink: #e0228b;
    --ink-grey: #555b61;
    --band-text: #e9f1f9;
  }
  * { margin: 0; padding: 0; box-sizing: border-box; }
  html, body { width: 1200px; height: 997px; overflow: hidden; }
  body { background: var(--stage); position: relative; font-family: "Arimo", Arial, sans-serif; }

  .card {
    position: absolute; left: 250px; width: 700px; height: 400px;
    background: linear-gradient(180deg, var(--paper) 0%, var(--paper-shade) 100%);
    overflow: hidden;
  }
  .card--front { top: 70px; }
  .card--contact { top: 527px; }

  .band {
    position: absolute; left: 0; right: 0; bottom: 0;
    background: linear-gradient(180deg, var(--band-blue) 0%, var(--band-blue-deep) 100%);
  }
  .pink-rule { position: absolute; left: 0; right: 0; height: 4px; background: var(--accent-pink); }
  .notch { position: absolute; width: 0; height: 0;
    border-left: 9px solid transparent; border-right: 9px solid transparent;
    border-top: 9px solid var(--accent-pink); }

  .company { position: absolute; left: 0; right: 0; text-align: center; font-family: "Arimo", Arial, sans-serif; }
  .company__name { font-weight: 700; color: var(--brand-blue); letter-spacing: 4px; text-transform: uppercase; line-height: 1.1; }
  .company__line { color: var(--ink-grey); letter-spacing: 1px; margin-top: 8px; }

  /* front */
  .card--front .pink-rule { top: 276px; }
  .card--front .band { top: 286px; }
  .card--front .notch { left: 341px; top: 286px; }
  .card--front .company { top: 112px; }
  .card--front .company__name { font-size: 38px; }
  .card--front .company__line { font-size: 16px; }
  .web { position: absolute; top: 334px; left: 0; right: 0; text-align: center;
    color: var(--band-text); font-size: 17px; letter-spacing: 3px; }

  /* contact */
  .card--contact .pink-rule { top: 170px; }
  .card--contact .band { top: 180px; }
  .card--contact .notch { left: 40px; top: 180px; }
  .card--contact .company { top: 58px; }
  .card--contact .company__name { font-size: 28px; }
  .card--contact .company__line { font-size: 13px; margin-top: 6px; }
  .person { position: absolute; left: 40px; top: 206px; color: var(--band-text); }
  .person__name { font-size: 26px; }
  .person__role { font-size: 14px; margin-top: 2px; }
  .contacts { position: absolute; left: 40px; top: 282px; list-style: none; color: var(--band-text); font-size: 16px; }
  .contacts li { display: flex; align-items: center; gap: 14px; height: 30px; }
  .contacts svg { width: 16px; height: 16px; fill: var(--band-text); }
  .address { position: absolute; right: 34px; top: 198px; text-align: right; color: var(--band-text); font-size: 14px; line-height: 1.35; }
  .address__org { font-size: 16px; margin-bottom: 2px; }
</style>
</head>
<body>
  <section class="card card--front">
    <div class="company">
      <p class="company__name">Pingrui Homemaking</p>
      <p class="company__line">Homemaking Training School</p>
    </div>
    <div class="pink-rule"></div>
    <div class="band"></div>
    <div class="notch"></div>
    <p class="web">www.prt2019.example</p>
  </section>

  <section class="card card--contact">
    <div class="company">
      <p class="company__name">Pingrui Homemaking</p>
      <p class="company__line">Homemaking Training School</p>
    </div>
    <div class="pink-rule"></div>
    <div class="band"></div>
    <div class="notch"></div>
    <div class="person">
      <p class="person__name">Marcus Dole</p>
      <p class="person__role">Chairman</p>
    </div>
    <ul class="contacts">
      <li><svg viewBox="0 0 16 16" aria-hidden="true"><path d="M2 6c0-2 2-3 6-3s6 1 6 3v1h-3V5.5H5V7H2zM4 8h8l2 5H2z"/></svg>0574-71948263</li>
      <li><svg viewBox="0 0 16 16" aria-hidden="true"><path d="M5 1h6a1 1 0 0 1 1 1v12a1 1 0 0 1-1 1H5a1 1 0 0 1-1-1V2a1 1 0 0 1 1-1zm0 2v9h6V3zm3 10a.8.8 0 1 0 0 .01z"/></svg>13857420916</li>
      <li><svg viewBox="0 0 16 16" aria-hidden="true"><path d="M1 3h14v10H1zm1.5 1.3v.4L8 8.6l5.5-3.9v-.4zM2.5 6.3v5.2h11V6.3L8 10.2z"/></svg>kelvora@mailnest.example</li>
    </ul>
    <div class="address">
      <p class="address__org">Pingrui Homemaking</p>
      <p>No.258, LanpingJie, BeiyuanQu</p>
      <p>Ningbo, Zhejiang</p>
    </div>
  </section>
</body>
</html>
```